****Business Card Design for Quarrystone Development. Design based around attached logo/company name

I’m looking for business card design for my company Quarrystone Development Group,LLC. Design should be professional, sharp and minimal. Outside of the attached logos, greyscale colors for remainder of cards. My thoughts are two-sided card with attached logo on one side and my info on the other but open to one-sided as well with right design.
Target Market(s)
Real estate professionals including banks, private investors, property owners, developers, commercial tenants like Brewlantern, Grovika or Tanquist’s.
Industry/Entity Type
Commercial real estate development and investments.
Contact Information for Business Card
Name, title, email, phone #’s, web address and physical address
Font styles to use
Other font styles liked:
- Helvetica, Garamond, etc
Colors
Designer to choose only greyscale colors for use in the design.
Requirements
Must have
- Attached logo first or second options.
Nice to have
- Two sided card with logo on one side. Attached Logo/company name can be laid out any way that flows as long as it’s legible.name
Should not have
- No loud colors. ***Please do not include logo, I have removed the company design with a logo image.

```html
<!DOCTYPE html>
<html lang="en">
<head>
<meta charset="utf-8">
<title>Quarrystone Development Group, LLC — Business Card</title>
<link rel="stylesheet" href="https://fonts.googleapis.com/css2?family=EB+Garamond:wght@500;700&family=Arimo:wght@400&display=swap">
<style>
  :root {
    --backdrop: #c9c9c9;
    --card-white: #ffffff;
    --slate: #5b6576;
    --slate-dark: #4b5466;
    --mid-grey: #8e9095;
    --text-grey: #6f7178;
    --emboss-light: #8691a2;
  }
  * { margin: 0; padding: 0; box-sizing: border-box; }
  html, body { width: 1200px; height: 788px; overflow: hidden; }
  body {
    background: var(--backdrop);
    display: flex;
    align-items: center;
    justify-content: center;
    gap: 44px;
  }
  .card {
    position: relative;
    width: 530px;
    height: 302px;
    border-radius: 18px;
    overflow: hidden;
  }
  .card--front { background: var(--card-white); }
  .card--back { background: var(--slate); display: flex; align-items: center; justify-content: center; }

  .edge-band {
    position: absolute;
    top: 0; right: 0;
    width: 24px; height: 100%;
  }

  .holder {
    position: absolute;
    top: 30px; right: 52px;
    text-align: right;
  }
  .holder__name {
    font-family: "EB Garamond", serif;
    font-weight: 700;
    font-size: 19px;
    letter-spacing: 1px;
    color: var(--slate-dark);
    text-transform: uppercase;
  }
  .holder__title {
    font-family: Arimo, sans-serif;
    font-size: 12px;
    color: var(--text-grey);
    margin-top: 2px;
  }

  .company {
    position: absolute;
    left: 34px; top: 112px;
    font-family: "EB Garamond", serif;
    font-weight: 500;
    color: var(--slate);
    line-height: 1.05;
  }
  .company__main { font-size: 33px; letter-spacing: 1px; text-transform: uppercase; }
  .company__sub { font-size: 14px; letter-spacing: 2px; text-transform: uppercase; }

  .contact {
    position: absolute;
    left: 34px; bottom: 26px;
    font-family: Arimo, sans-serif;
    font-size: 12px;
    color: var(--text-grey);
    line-height: 1.45;
    list-style: none;
  }
  .contact__address { margin-bottom: 6px; }
  .contact__item { display: flex; align-items: center; gap: 7px; }
  .contact__item svg { width: 10px; height: 10px; flex: none; }

  .company--back {
    font-family: "EB Garamond", serif;
    font-weight: 500;
    color: var(--emboss-light);
    text-align: center;
    line-height: 1.05;
  }
  .company--back .company__main { font-size: 52px; letter-spacing: 2px; }
  .company--back .company__sub { font-size: 20px; letter-spacing: 3px; }
</style>
</head>
<body>
  <section class="card card--front">
    <svg class="edge-band" viewBox="0 0 24 302" preserveAspectRatio="none" aria-hidden="true">
      <rect x="0" y="0" width="24" height="90" fill="var(--slate)"/>
      <rect x="0" y="96" width="24" height="28" fill="var(--mid-grey)"/>
      <rect x="0" y="130" width="24" height="172" fill="var(--slate)"/>
    </svg>

    <div class="holder">
      <p class="holder__name">Adrian Veller</p>
      <p class="holder__title">Founder/CEO</p>
    </div>

    <div class="company">
      <p class="company__main">Quarrystone</p>
      <p class="company__sub">Development Group, LLC</p>
    </div>

    <ul class="contact">
      <li class="contact__address">5120 Ledgemoor Avenue<br>Halvern AB 3926</li>
      <li class="contact__item">
        <svg viewBox="0 0 10 10" aria-hidden="true"><path d="M2 1 L4 1 L4.6 3 L3.5 3.8 Q4.5 5.8 6.2 6.5 L7 5.4 L9 6 L9 8 Q5 9 1.5 4.5 Q1 2.5 2 1 Z" fill="var(--slate)"/></svg>
        (123)-555-0192
      </li>
      <li class="contact__item">
        <svg viewBox="0 0 10 10" aria-hidden="true"><rect x="0.5" y="2" width="9" height="6.5" fill="var(--slate)"/><path d="M0.5 2 L5 5.6 L9.5 2" fill="none" stroke="#fff" stroke-width="0.8"/></svg>
        info@quarrystonedev.com
      </li>
      <li class="contact__item">
        <svg viewBox="0 0 10 10" aria-hidden="true"><circle cx="5" cy="5" r="4.5" fill="var(--slate)"/><path d="M0.5 5 H9.5 M5 0.5 V9.5" stroke="#fff" stroke-width="0.6"/><ellipse cx="5" cy="5" rx="2" ry="4.5" fill="none" stroke="#fff" stroke-width="0.6"/></svg>
        www.quarrystonedev.com
      </li>
    </ul>
  </section>

  <section class="card card--back">
    <div class="company--back">
      <p class="company__main">QUARRYSTONE</p>
      <p class="company__sub">DEVELOPMENT GROUP, LLC</p>
    </div>
  </section>
</body>
</html>
```